Roofing Contractor business card redesign

I want to redesign my business card with a fresh, eye catching concept

Target Market(s)

Residential Roofing Clients, potential employees, and subcontractors.

Industry/Entity Type

Business

Colors

Designer to choose colors to be used in the design.

Requirements
Nice to have
• I just want something that's more pleasing to the eye. You can use a combination of either / or of my logos.

```html
<!DOCTYPE html>
<html lang="en">
<head>
<meta charset="utf-8">
<title>Fair Hands Builders – Business Card</title>
<link href="https://fonts.googleapis.com/css2?family=Oswald:wght@700&family=Roboto+Condensed:wght@400;700&display=swap" rel="stylesheet">
<style>
  :root {
    --stage: #e9e5df;
    --card-white: #fbfaf8;
    --card-black: #1d1e1f;
    --maroon: #4a1210;
    --maroon-dark: #3a0d0b;
    --ink: #2a2a2a;
    --accent: #e8772a;
    --art-warm: #f1e3cf;
    --art-cool: #ece9e4;
    --white: #ffffff;
  }
  * { margin: 0; padding: 0; box-sizing: border-box; }
  html, body { width: 1200px; height: 911px; overflow: hidden; }
  body {
    background: var(--stage);
    font-family: "Roboto Condensed", "Arial Narrow", sans-serif;
    position: relative;
  }
  .card {
    position: absolute;
    left: 270px;
    width: 660px;
    height: 400px;
    border-radius: 22px;
    overflow: hidden;
    box-shadow: 0 6px 18px rgba(0,0,0,.18);
  }
  /* Front */
  .card-front { top: 40px; background: var(--card-white); }
  .front-art {
    position: absolute; right: 0; top: 0; width: 300px; height: 400px;
    background: radial-gradient(ellipse at 55% 45%, var(--art-warm) 0%, var(--art-cool) 60%, var(--card-white) 100%);
  }
  .front-band {
    position: absolute; left: 0; top: 0; width: 84px; height: 100%;
    background: linear-gradient(90deg, var(--maroon-dark) 0%, var(--maroon) 100%);
  }
  .front-mark {
    position: absolute; left: 38px; top: 40px; width: 92px; height: 92px;
    border-radius: 50%; background: var(--card-white); border: 4px solid var(--maroon-dark);
  }
  .front-info { position: absolute; left: 160px; top: 48px; }
  .brand-name {
    font-family: "Oswald", "Arial Narrow", sans-serif; font-weight: 700;
    font-size: 38px; line-height: 1; color: var(--maroon); letter-spacing: -.5px;
  }
  .brand-sub { font-size: 15px; font-weight: 700; color: var(--ink); margin-top: 4px; }
  .person-name { font-size: 24px; color: var(--ink); margin-top: 22px; letter-spacing: .5px; }
  .person-title { font-size: 17px; color: var(--accent); line-height: 1.2; margin-top: 4px; }
  .address { font-size: 16px; color: var(--ink); line-height: 1.25; margin-top: 10px; }
  .contacts { list-style: none; font-size: 15px; color: var(--ink); margin-top: 10px; }
  .contacts li { display: flex; align-items: center; gap: 8px; line-height: 1.3; }
  .contacts svg { width: 12px; height: 12px; fill: var(--ink); }
  /* Back */
  .card-back { top: 470px; background: var(--card-black); }
  .back-url {
    position: absolute; left: 0; top: 56px; width: 100%; text-align: center;
    color: var(--white); font-size: 15px; letter-spacing: 9px;
  }
  .back-lockup {
    position: absolute; left: 0; top: 138px; width: 100%;
    display: flex; justify-content: center; align-items: center; gap: 14px;
  }
  .back-word {
    font-family: "Oswald", "Arial Narrow", sans-serif; font-weight: 700;
    font-size: 78px; line-height: 1; color: var(--white);
  }
  .back-mark { width: 64px; height: 64px; border-radius: 50%; background: var(--accent); }
  .back-sub {
    position: absolute; left: 0; top: 244px; width: 100%; text-align: center;
    color: var(--white); font-size: 30px; font-weight: 700;
  }
</style>
</head>
<body>
  <section class="card card-front">
    <div class="front-art" role="img" aria-label="Faint illustration of three cheerful roofing workers"></div>
    <div class="front-band"></div>
    <div class="front-mark"></div>
    <div class="front-info">
      <div class="brand-name">Fair Hands</div>
      <div class="brand-sub">Builders, Inc.</div>
      <div class="person-name">SAM RIVERA</div>
      <div class="person-title">Keller Certified Roof Inspector<br>Licensed Property Adjuster</div>
      <div class="address">4410 Oak Bend Road Suite 118<br>Plano, TX 75024</div>
      <ul class="contacts">
        <li><svg viewBox="0 0 12 12"><path d="M2 1l2 0 1 3-1.5 1a7 7 0 0 0 3.5 3.5L8 7l3 1v2a1 1 0 0 1-1 1A9 9 0 0 1 1 2a1 1 0 0 1 1-1z"/></svg>(555) 214-3000</li>
        <li><svg viewBox="0 0 12 12"><path d="M3 0h6a1 1 0 0 1 1 1v10a1 1 0 0 1-1 1H3a1 1 0 0 1-1-1V1a1 1 0 0 1 1-1zm0 2v7h6V2z"/></svg>(555) 610-2847</li>
        <li><svg viewBox="0 0 12 12"><path d="M0 2h12v8H0zm1 1v.4l5 3.2 5-3.2V3z"/></svg>sam@fairhandstx.com</li>
        <li><svg viewBox="0 0 12 12"><circle cx="6" cy="6" r="6"/></svg>www.fairhandstx.com</li>
      </ul>
    </div>
  </section>

  <section class="card card-back">
    <div class="back-url">www.fairhandstx.com</div>
    <div class="back-lockup">
      <span class="back-word">Fair</span>
      <span class="back-mark"></span>
      <span class="back-word">Hands</span>
    </div>
    <div class="back-sub">Builders, Inc.</div>
  </section>
</body>
</html>
```